Website Design for The Elder Nook

Please design and code a new website.
Here are the sites I like best:
http://www.voyaglint.com/alternate/
http://www.wheelgiftbay.org
Please make it similar but look at the competitor site (below) for images and wording. This is NOT a car donation site. It's a senior lead placement site like https://www.kinhavenfinder.com. I just like this sites above as a lead generation sites.
Competitor site:
https://www.kinhavenfinder.com (use ideas / verbiage from this site)
Updates
Competitor site:
Coding
Coded - Design and coding required
Number of Pages Required
1 page
Look and feel
Each slider illustrates characteristics of the customer's brand and the style your logo design should communicate.

```html
<!DOCTYPE html>
<html lang="en">
<head>
<meta charset="utf-8">
<title>The Elder Nook – Senior Living Advice</title>
<link rel="stylesheet" href="https://fonts.googleapis.com/css2?family=Lora:ital,wght@0,400;1,400&family=Jost:wght@300;400&display=swap">
<style>
:root{
  --blue:#0f5bb3;
  --blue-dark:#0b4f9e;
  --green:#8cc63f;
  --green-text:#7cbf35;
  --ink:#2b2b2b;
  --muted:#777;
  --line:#e3e3e3;
  --white:#fff;
}
*{box-sizing:border-box;margin:0;padding:0}
html,body{width:1200px;height:3040px;overflow:hidden}
body{font-family:"Jost",sans-serif;font-weight:300;color:var(--ink);background:var(--white);position:relative}
.abs{position:absolute}
a{color:inherit;text-decoration:none}
h2,h3{font-weight:400}

/* header */
.site-header{position:absolute;left:0;top:0;width:1200px;height:91px}
.brand{position:absolute;left:88px;top:28px;display:flex;align-items:center;gap:10px;font-family:"Lora",serif;font-size:25px;color:var(--blue)}
.brand-dot{width:26px;height:26px;border-radius:50%;background:var(--green)}
.call{position:absolute;left:625px;top:22px;display:flex;gap:10px;align-items:center}
.call small{display:block;font-family:"Lora",serif;font-size:11px;color:#333}
.call strong{display:block;font-weight:400;font-size:23px;color:#222}
.badge{position:absolute;left:858px;top:22px;width:95px;height:48px;background:var(--blue);border-radius:3px}
.lang{position:absolute;left:1011px;top:28px;width:101px;height:35px;border:1px solid var(--line);font-size:13px;display:flex;align-items:center;gap:6px;padding-left:12px}
.lang i{width:32px;height:17px;background:linear-gradient(#c9302c 0 50%,#fff 50% 60%,#c9302c 60%);position:relative}
.lang i:before{content:"";position:absolute;left:0;top:0;width:14px;height:9px;background:#2b3f8c}

/* nav */
.main-nav{position:absolute;left:0;top:91px;width:1200px;height:42px;background:var(--blue);display:flex;padding-left:88px}
.main-nav a{font-family:"Lora",serif;font-size:12.5px;color:#fff;text-transform:uppercase;padding:0 20px;line-height:42px;border-right:1px solid rgba(255,255,255,.18)}
.main-nav a.active{background:var(--blue-dark);border-bottom:3px solid var(--green)}

/* hero */
.hero{position:absolute;left:0;top:133px;width:1200px;height:573px;background:linear-gradient(180deg,#c9d0d6 0%,#dde1e3 55%,#cfc9c2 100%)}
.hero-line{position:absolute;left:430px;top:382px;width:340px;text-align:center;font-family:"Lora",serif;font-size:28px;line-height:42px;color:#222}
.inquiry{position:absolute;left:783px;top:210px;width:329px;height:418px;background:#fff;padding:10px}
.inquiry-head{background:var(--green);height:72px;clip-path:polygon(0 0,100% 0,100% 80%,50% 100%,0 80%);color:#fff;font-family:"Lora",serif;font-size:25px;text-align:center;padding-top:18px}
.field{margin-top:12px;height:42px;border:1px solid #ddd;border-radius:3px;display:flex;font-size:13px;color:#666}
.field span{width:40px;border-right:1px solid #ddd;display:flex;align-items:center;justify-content:center}
.field p{padding:0 16px;line-height:40px}
.field.tall{height:70px}
.submit{margin-top:18px;height:38px;background:var(--blue);color:#fff;font-family:"Lora",serif;font-size:15px;text-align:center;line-height:38px;border-radius:3px}

/* section titles */
.title{position:absolute;left:0;width:1200px;text-align:center;font-family:"Lora",serif;font-size:29px;color:var(--blue)}
.title em{font-style:normal;color:var(--green-text)}
.lead{position:absolute;left:190px;width:820px;text-align:center;font-size:14.5px;line-height:24px;color:#333}

/* support cards */
.features{position:absolute;left:142px;top:900px;display:flex;gap:14px}
.feature{width:172px;height:180px;border:1px solid #ddd;box-shadow:0 2px 4px rgba(0,0,0,.06);text-align:center;padding:24px 22px 0;font-size:18px;line-height:21px;color:#333}
.feature svg{display:block;margin:0 auto 8px}

.nocost{position:absolute;top:1128px;left:142px;width:918px;display:flex;align-items:center}
.nocost h3{font-family:"Lora",serif;font-size:24px;color:var(--blue);width:284px}
.nocost h3 em{font-style:normal;color:var(--green-text)}
.nocost p{font-size:17px;line-height:25px;width:445px}
.nocost a{font-size:21px;color:var(--blue);margin-left:auto}

/* advisor */
.advisor{position:absolute;left:0;top:1251px;width:1200px;height:481px;background:linear-gradient(90deg,#1a5fb0,#2769b8 30%,#1b5fae 60%,#1861b3);color:#fff}
.advisor h2{position:absolute;top:75px;width:1200px;text-align:center;font-family:"Lora",serif;font-size:28px}
.advisor .sub{position:absolute;top:125px;width:1200px;text-align:center;font-size:14.5px}
.points{position:absolute;top:173px;left:240px;display:flex;gap:60px}
.point{width:200px;text-align:center;font-size:16px;line-height:21px}
.ring{width:98px;height:98px;border:1.5px solid #fff;border-radius:50%;margin:0 auto 12px;display:flex;align-items:center;justify-content:center}
.search{position:absolute;top:351px;left:298px;width:604px;height:45px;background:#fff;border-radius:3px;display:flex;align-items:center;padding:4px;color:#333;font-size:14.5px}
.search span{flex:1;padding-left:16px}
.search b{font-weight:400;font-family:"Lora",serif;width:222px;height:37px;line-height:37px;text-align:center;background:var(--green);color:#fff;font-size:15px;border-radius:2px}

/* testimonials */
.tests{position:absolute;top:1870px;left:142px;display:flex;gap:31px}
.test{width:285px;position:relative}
.test blockquote{border:1px solid #e5e5e5;height:148px;padding:14px 17px;font-size:12.8px;line-height:21.5px;color:#888;letter-spacing:.2px}
.test .who{position:absolute;left:10px;top:125px;display:flex;align-items:center;gap:20px;font-family:"Lora",serif;font-size:14.5px;color:#333}
.avatar{width:70px;height:70px;border-radius:50%;border:3px solid var(--blue);background:linear-gradient(#e8d9c6,#b89c80)}
.who span{margin-top:-6px}
.btn{position:absolute;background:var(--green);color:#fff;font-family:"Lora",serif;font-size:15px;text-align:center;border-radius:2px}

/* veterans */
.veterans{position:absolute;top:2215px;left:0;width:1200px;height:291px;background:linear-gradient(180deg,#2a2d45 0%,#3a2030 40%,#4a1a1f 75%,#241a1c 100%);color:#fff;text-align:center}
.veterans h2{position:absolute;top:88px;width:1200px;font-family:"Lora",serif;font-size:25px}
.veterans p{position:absolute;top:127px;width:1200px;font-size:14.5px;line-height:24px}

/* states */
.states{position:absolute;top:2638px;left:158px;display:flex}
.states ul{list-style:none;font-size:13px;line-height:22px;color:#333}
.states li:before{content:"› ";}

/* footer */
.site-footer{position:absolute;top:2872px;left:0;width:1200px;height:168px;background:var(--blue);color:#fff}
.foot-nav{position:absolute;top:47px;width:1200px;display:flex;justify-content:center;gap:33px;font-family:"Lora",serif;font-size:11px;text-transform:uppercase}
.foot-rule{position:absolute;top:112px;left:142px;width:918px;border-top:1px solid rgba(255,255,255,.25)}
.copy{position:absolute;top:128px;left:142px;font-size:13px}
.social{position:absolute;top:125px;left:944px;display:flex;gap:6px}
.social i{width:24px;height:24px;border-radius:50%;border:1.5px solid #fff;background:rgba(255,255,255,.15)}
</style>
</head>
<body>

<header class="site-header">
  <div class="brand"><span class="brand-dot"></span>The Elder Nook</div>
  <div class="call">
    <svg width="34" height="34" viewBox="0 0 24 24" fill="none" stroke="#0f5bb3" stroke-width="1.4"><path d="M5 3h4l2 5-2.5 1.5a11 11 0 0 0 6 6L16 13l5 2v4a2 2 0 0 1-2 2A17 17 0 0 1 3 5a2 2 0 0 1 2-2z"/><path d="M15 3a6 6 0 0 1 6 6M15 7a2 2 0 0 1 2 2"/></svg>
    <div><small>Talk to a local advisor for FREE</small><strong>(555) 014-3827</strong></div>
  </div>
  <div class="badge" role="img" aria-label="Accreditation badge"></div>
  <div class="lang">EN : <i></i> <svg width="9" height="6" viewBox="0 0 9 6"><path d="M1 1l3.5 3.5L8 1" stroke="#333" fill="none"/></svg></div>
</header>

<nav class="main-nav">
  <a class="active">Assisted Living</a><a>Memory Care</a><a>Nursing Homes</a><a>More Living Options ⌄</a><a>Planning &amp; Advice</a><a>How Our Service Works</a>
</nav>

<section class="hero" role="img" aria-label="Photo of a smiling senior couple walking bicycles on a beach"></section>
<p class="hero-line">You know your family.<br>We know <i>Senior Living</i>.</p>

<form class="inquiry">
  <div class="inquiry-head">Quick Inquiry</div>
  <div class="field"><span>●</span><p>Name</p></div>
  <div class="field"><span>✆</span><p>Phone</p></div>
  <div class="field"><span>✉</span><p>Email</p></div>
  <div class="field tall"><span style="align-items:flex-start;padding-top:12px">▬</span><p>Message</p></div>
  <div class="submit">Submit Now</div>
</form>

<h2 class="title" style="top:780px"><em>The Support You Need To</em> Make The Right Choice</h2>
<p class="lead" style="top:828px">Lorem ipsum dolor sit amet, consectetuer adipiscing elit, sed diam nonummy nibh euismod tincidunt ut laoreet dolore magna<br>aliquam erat volutpat. Ut wisi enim ad minim veniam, quis nostrud exerci tation ullamcorper suscipit.</p>

<div class="features">
  <div class="feature"><svg width="54" height="56" viewBox="0 0 54 56" fill="none" stroke="#7cbf35" stroke-width="1.6"><circle cx="27" cy="14" r="9"/><path d="M10 54V36a8 8 0 0 1 8-8h18a8 8 0 0 1 8 8v18M22 28l5 12 5-12M20 54V42M34 54V42"/></svg>Dedicated local advisor</div>
  <div class="feature" style="padding-left:12px;padding-right:12px"><svg width="54" height="56" viewBox="0 0 54 56" fill="none" stroke="#7cbf35" stroke-width="1.6"><path d="M4 28L27 6l23 22M10 22v32h34V22M22 54V40h10v14M22 26h10v8H22z"/></svg>Hand-picked list of communities to match your needs</div>
  <div class="feature"><svg width="54" height="56" viewBox="0 0 54 56" fill="none" stroke="#7cbf35" stroke-width="1.6"><circle cx="30" cy="22" r="10"/><path d="M30 15v14M33 17h-5a2 2 0 0 0 0 4h4a2 2 0 0 1 0 4h-5M30 2v5M24 4l1 4M36 4l-1 4M4 46l10-8h12l8 4H22M4 54l12-4 20 2 14-12"/></svg>Full details and<br>pricing</div>
  <div class="feature"><svg width="54" height="56" viewBox="0 0 54 56" fill="none" stroke="#7cbf35" stroke-width="1.6"><rect x="3" y="8" width="48" height="46"/><path d="M3 18h48M14 3v9M40 3v9M11 26h32v20H11zM19 26v20M27 26v20M35 26v20M11 33h32M11 40h32"/></svg>Help scheduling<br>tours</div>
  <div class="feature"><svg width="64" height="56" viewBox="0 0 64 56" fill="none" stroke="#7cbf35" stroke-width="1.6"><path d="M14 10h30v32H14zM44 22h10l8 10v10H44M2 18h10M4 26h8M6 34h6"/><circle cx="22" cy="44" r="5"/><circle cx="52" cy="44" r="5"/></svg>Move in<br>support</div>
</div>

<div class="nocost">
  <h3><em>There's</em> No Cost To You.</h3>
  <p>We work with over 20,000 senior living communities.<br>Our community partners pay us for placement services.</p>
  <a>Call (555) 014-3827</a>
</div>

<section class="advisor">
  <div class="abs" style="inset:0;background:linear-gradient(90deg,rgba(10,60,140,.25),rgba(40,110,190,.15),rgba(10,60,140,.25))" role="img" aria-label="Row of portrait photos of local advisors tinted blue"></div>
  <h2>Your local advisor informs. You decide.</h2>
  <p class="sub">Lorem ipsum dolor sit amet, consectetuer adipiscing elit, sed diam nonummy nibh euismod tincidunt ut laoreet.</p>
  <div class="points">
    <div class="point"><div class="ring"><svg width="34" height="60" viewBox="0 0 34 60" fill="none" stroke="#fff" stroke-width="1.6"><circle cx="17" cy="14" r="11"/><path d="M17 25v32"/></svg></div>Insider's tips for the area<br>near you</div>
    <div class="point"><div class="ring"><svg width="54" height="48" viewBox="0 0 54 48" fill="none" stroke="#fff" stroke-width="1.8"><path d="M27 44S3 30 3 15A11 11 0 0 1 27 10a11 11 0 0 1 24 5c0 15-24 29-24 29z"/></svg></div>Advice tailored to your<br>unique situation</div>
    <div class="point"><div class="ring"><svg width="54" height="44" viewBox="0 0 54 44" fill="none" stroke="#fff" stroke-width="1.6"><circle cx="5" cy="6" r="4"/><circle cx="5" cy="22" r="4"/><circle cx="5" cy="38" r="4"/><path d="M16 6h36M16 22h36M16 38h36"/></svg></div>Time saving know-how and<br>resources</div>
  </div>
  <div class="search"><span>Enter city or postal code</span><b>Find an advisor near you</b></div>
</section>

<h2 class="title" style="top:1806px"><em>93% Of Our Customers</em> Recommend Our Service</h2>
<div class="tests">
  <div class="test"><blockquote>Lorem ipsum dolor sit amet, consectetuer adipiscing elit, sed diam nonummy nibh euismod tincidunt ut laoreet dolore magna aliquam erat volutpat. Ut wisi enim ad minim veniam, quis nostrud.</blockquote><div class="who"><div class="avatar" role="img" aria-label="Portrait of Marla Quint"></div><span>Marla Quint</span></div></div>
  <div class="test"><blockquote>Lorem ipsum dolor sit amet, consectetuer adipiscing elit, sed diam nonummy nibh euismod tincidunt ut laoreet dolore magna aliquam erat volutpat. Ut wisi enim ad minim veniam, quis nostrud.</blockquote><div class="who"><div class="avatar" role="img" aria-label="Portrait of Devon Hale"></div><span>Devon Hale</span></div></div>
  <div class="test"><blockquote>Lorem ipsum dolor sit amet, consectetuer adipiscing elit, sed diam nonummy nibh euismod tincidunt ut laoreet dolore magna aliquam erat volutpat. Ut wisi enim ad minim veniam, quis nostrud.</blockquote><div class="who"><div class="avatar" role="img" aria-label="Portrait of Nora Pell"></div><span>Nora Pell</span></div></div>
</div>
<a class="btn" style="top:2093px;left:496px;width:208px;height:38px;line-height:38px">See More Testimonials</a>

<section class="veterans" role="img" aria-label="Waving American flag background">
  <h2>Access Up To $2,000 Per Month In Veteran's Aid</h2>
  <p>We work with Veterans every day. Most veteran families do not know of a key benefit available to them and their families.<br>It's called the Veteran's Aid and Attendance benefit. This benefit can help pay for senior living and home care.</p>
  <a class="btn" style="top:176px;left:535px;width:130px;height:38px;line-height:38px">Learn More</a>
</section>

<h2 class="title" style="top:2580px"><em>Senior Assisted</em> Living by State</h2>
<div class="states">
  <ul style="width:142px"><li>Alabama</li><li>Arizona</li><li>Arkansas</li><li>California</li><li>Colorado</li><li>Connecticut</li><li>Delaware</li></ul>
  <ul style="width:185px"><li>District of Columbia</li><li>Florida</li><li>Georgia</li><li>Hawaii</li><li>Idaho</li><li>Illinois</li><li>Indiana</li></ul>
  <ul style="width:158px"><li>Iowa</li><li>Kansas</li><li>Kentucky</li><li>Louisiana</li><li>Maine</li><li>Maryland</li><li>Massachusetts</li></ul>
  <ul style="width:136px"><li>Michigan</li><li>Minnesota</li><li>Mississippi</li><li>Missouri</li><li>Montana</li><li>Nebraska</li><li>Nevada</li></ul>
  <ul style="width:169px"><li>New Hampshire</li><li>New Jersey</li><li>New Mexico</li><li>New York</li><li>North Carolina</li><li>North Dakota</li><li>Ohio</li></ul>
  <ul><li>Oklahoma</li><li>Oregon</li><li>Pennsylvania</li><li>Rhode Island</li><li>South Carolina</li><li>South Dakota</li><li>Tennessee</li></ul>
</div>

<footer class="site-footer">
  <div class="foot-nav"><a>Assisted Living</a><a>Memory Care</a><a>Nursing Homes</a><a>More Living Options ⌄</a><a>Planning &amp; Advice</a><a>How Our Service Works</a></div>
  <div class="foot-rule"></div>
  <p class="copy">Copyright 2019 The Elder Nook. All Rights Reserved.</p>
  <div class="social"><i></i><i></i><i></i><i></i></div>
</footer>

</body>
</html>
```